Business Card Design

We would like to re-design our business cards. Our Company - Qwinrel Turbochargers, rebuilds turbochargers and sells replacement parts. Our website is: http://www.qwinrelturbochargers-example.com
We just had our logo changed. I will attach the file. Looking for fresh new/modern business card. We like the colors red, black, white and silver. Black background looks attractive, but not a requirement. The final design should communicate reasonable/competitive prices, top quality and reliability of our products.
Updates
Project Deadline Extended
Reason: Need to finalize the info on the card. Currently working on changing address and email info. Want to make sure it is the correct one before accepting the final design. Unless, this is something that can be changed at a later time..??
Industry/Entity Type
Business
Contact Information for Business Card
QWINREL TURBOCHARGERS, LLC
20473 Harwick Lane NE
Massillon, OH 44647
Tel: +1-555-214-7390
Fax: +1-555-267-1842
info@QwinrelTurbochargers-example.com
Our current business card had the following highlights:
*We rebuild all Turbocharges for Automotive, Diesel and Industrial
*Precision Balancing and in-house turbocharger needs
*All Turbocharger replacement parts are made in USA / U.K.
Look and feel
Each slider illustrates characteristics of the customer's brand and the style your logo design should communicate.

```html
<!DOCTYPE html>
<html lang="en">
<head>
<meta charset="utf-8">
<title>Qwinrel Turbochargers – Business Card</title>
<link href="https://fonts.googleapis.com/css2?family=Open+Sans:wght@400;600;800&display=swap" rel="stylesheet">
<style>
  :root {
    --bg: #e9e6e1;
    --card-black: #141213;
    --brand-red: #e8252f;
    --brand-red-soft: #f0656b;
    --white: #ffffff;
    --silver: #c9c9c9;
    --arc: #3a2a2a;
  }
  html, body {
    margin: 0;
    padding: 0;
    width: 1200px;
    height: 1023px;
    overflow: hidden;
    background: var(--bg);
    font-family: "Open Sans", Arial, sans-serif;
  }
  .stage {
    position: relative;
    width: 1200px;
    height: 1023px;
  }
  .card {
    position: absolute;
    width: 560px;
    height: 320px;
    border-radius: 4px;
    overflow: hidden;
    box-shadow: 0 10px 28px rgba(0,0,0,0.28);
    background: var(--card-black);
  }
  .card-front { left: 320px; top: 150px; }
  .card-back  { left: 320px; top: 553px; }
  .card-art {
    position: absolute;
    inset: 0;
    width: 100%;
    height: 100%;
  }
  .brand {
    position: absolute;
    display: flex;
    align-items: center;
    gap: 10px;
    font-weight: 800;
    white-space: nowrap;
  }
  .brand-mark {
    width: 13px;
    height: 13px;
    background: var(--brand-red);
  }
  .front-brand {
    left: 30px;
    top: 48px;
    font-size: 22px;
    color: var(--card-black);
  }
  .address {
    position: absolute;
    right: 22px;
    top: 118px;
    text-align: right;
    font-style: normal;
    font-size: 12.5px;
    line-height: 1.45;
    color: var(--white);
    white-space: nowrap;
  }
  .person {
    position: absolute;
    left: 300px;
    top: 202px;
    color: var(--white);
  }
  .person-name {
    font-size: 21px;
    color: var(--brand-red-soft);
    margin: 0;
    font-weight: 400;
    line-height: 1.1;
    white-space: nowrap;
  }
  .person-role {
    font-size: 12px;
    margin: 2px 0 6px;
  }
  .contact-list {
    list-style: none;
    margin: 0;
    padding: 0;
    font-size: 12px;
    line-height: 1.55;
  }
  .contact-list li {
    display: flex;
    align-items: center;
    gap: 8px;
    white-space: nowrap;
  }
  .contact-icon {
    width: 11px;
    height: 11px;
    flex: none;
  }
  .back-brand {
    left: 0;
    right: 0;
    top: 118px;
    justify-content: center;
    font-size: 34px;
    color: var(--brand-red);
  }
  .back-brand .brand-mark { width: 20px; height: 20px; background: var(--silver); }
  .website {
    position: absolute;
    left: 40px;
    bottom: 34px;
    margin: 0;
    font-size: 14px;
    color: var(--brand-red-soft);
    letter-spacing: 0.3px;
  }
  .back-strip {
    position: absolute;
    left: 0;
    right: 40px;
    bottom: 0;
    height: 14px;
    background: var(--brand-red);
    border-radius: 0 7px 0 0;
  }
</style>
</head>
<body>
<main class="stage">

  <section class="card card-front" aria-label="Business card front">
    <svg class="card-art" viewBox="0 0 560 320" preserveAspectRatio="none" aria-hidden="true">
      <defs>
        <linearGradient id="frontBlack" x1="0" y1="0" x2="1" y2="1">
          <stop offset="0" stop-color="#2a2627"/>
          <stop offset="1" stop-color="#0f0d0e"/>
        </linearGradient>
      </defs>
      <rect width="560" height="320" fill="url(#frontBlack)"/>
      <path d="M0 0 H560 V34 C420 60 285 150 222 320 H0 Z" fill="#e8252f"/>
      <path d="M0 0 H540 C390 30 240 140 182 320 H0 Z" fill="#ffffff"/>
    </svg>

    <div class="brand front-brand">
      <span class="brand-mark"></span>
      <span class="brand-name">Qwinrel Turbochargers</span>
    </div>

    <address class="address">
      20473 Harwick Lane NE<br>
      Brenford, Ohio
    </address>

    <div class="person">
      <p class="person-name">Corwin Haledge</p>
      <p class="person-role">Director</p>
      <ul class="contact-list">
        <li>
          <svg class="contact-icon" viewBox="0 0 12 12" aria-hidden="true">
            <path d="M2 1 L4.5 1 L5.3 3.6 L3.9 4.6 C4.6 6.1 5.9 7.4 7.4 8.1 L8.4 6.7 L11 7.5 L11 10 C11 10.6 10.6 11 10 11 C5 11 1 7 1 2 C1 1.4 1.4 1 2 1 Z" fill="#e8252f"/>
          </svg>
          +1-555-214-7390
        </li>
        <li>
          <svg class="contact-icon" viewBox="0 0 12 12" aria-hidden="true">
            <rect x="3" y="1" width="6" height="3" fill="#e8252f"/>
            <rect x="1" y="4.5" width="10" height="4.5" rx="1" fill="#e8252f"/>
            <rect x="3" y="8" width="6" height="3" fill="#e8252f"/>
          </svg>
          +1-555-267-1842
        </li>
        <li>
          <svg class="contact-icon" viewBox="0 0 12 12" aria-hidden="true">
            <rect x="0.5" y="2" width="11" height="8" fill="#e8252f"/>
            <path d="M0.5 2 L6 6.5 L11.5 2" fill="none" stroke="#141213" stroke-width="1"/>
          </svg>
          info@QwinrelTurbochargers-example.com
        </li>
      </ul>
    </div>
  </section>

  <section class="card card-back" aria-label="Business card back">
    <svg class="card-art" viewBox="0 0 560 320" preserveAspectRatio="none" aria-hidden="true">
      <defs>
        <radialGradient id="backBlack" cx="0.45" cy="0.4" r="0.8">
          <stop offset="0" stop-color="#2b2728"/>
          <stop offset="1" stop-color="#0e0c0d"/>
        </radialGradient>
      </defs>
      <rect width="560" height="320" fill="url(#backBlack)"/>
      <path d="M20 60 C200 10 430 20 520 110 C470 60 260 40 40 80 Z" fill="#3a2a2a" opacity="0.8"/>
    </svg>

    <div class="brand back-brand">
      <span class="brand-mark"></span>
      <span class="brand-name">Qwinrel Turbochargers</span>
    </div>

    <p class="website">www.qwinrelturbochargers-example.com</p>
    <div class="back-strip"></div>
  </section>

</main>
</body>
</html>
```